Harbor Crestline (Business Card Design)

Need business cards designed. Something modern, chic, and sleek. Mabye the back of the card should be the navy blue that is in the logo and then just the logo on the back.

Target Market(s)

Those in the hotel, office, and renovation industry

Contact Information for Business Card

1. Logo 2. Dorian Fenwick 3. CEO/Founder 4. Phone: (833) HarbCre / (833) 427-2731 5. Email: dorian@theharborcrestline.com 6. Website: www.theharborcrestline.com

Font styles to use
Other font styles liked:
• Look at the logo font and base the font for everything else off of that.

Colors
0054AA
0677BA
7BADD7
CADEEF
E8F1F8

Requirements
Must have
• Colors that are associated in the logo
Nice to have
• Sleek modern clean and chic design.

```html
<!DOCTYPE html>
<html lang="en">
<head>
<meta charset="utf-8">
<title>Harbor Crestline — Business Cards</title>
<link rel="stylesheet" href="https://fonts.googleapis.com/css2?family=Montserrat:wght@500;600;700&family=Open+Sans:wght@400&display=swap">
<style>
  :root {
    --navy: #0f1a40;
    --gold: #d3a64a;
    --orange: #ee6a2a;
    --orange-light: #f39a25;
    --white: #ffffff;
    --backdrop: #e9eaee;
  }
  * { box-sizing: border-box; margin: 0; padding: 0; }
  html, body { width: 1200px; height: 947px; overflow: hidden; }
  body {
    background: var(--backdrop);
    position: relative;
    font-family: "Open Sans", Arial, sans-serif;
  }
  .card {
    position: absolute;
    width: 600px;
    height: 343px;
    border-radius: 22px;
    background: var(--navy);
    overflow: hidden;
    box-shadow: 0 14px 30px rgba(15, 26, 64, 0.25);
  }
  .card-back { left: 80px; top: 90px; }
  .card-front { left: 520px; top: 514px; }

  .brand {
    display: flex;
    align-items: center;
    gap: 12px;
    font-family: "Montserrat", Arial, sans-serif;
    font-weight: 600;
    color: var(--white);
    text-transform: uppercase;
    letter-spacing: 0.12em;
    white-space: nowrap;
  }
  .brand-square { background: var(--gold); flex: none; }

  .card-back .brand {
    position: absolute;
    left: 50%; top: 50%;
    transform: translate(-50%, -50%);
    font-size: 34px;
  }
  .card-back .brand-square { width: 22px; height: 22px; }

  .swoosh { position: absolute; inset: 0; }

  .name-block {
    position: absolute;
    right: 58px; top: 30px;
    text-align: right;
  }
  .name {
    font-family: "Montserrat", Arial, sans-serif;
    font-weight: 700;
    font-size: 26px;
    color: var(--gold);
    line-height: 1.1;
  }
  .role {
    font-family: "Open Sans", Arial, sans-serif;
    font-size: 15px;
    color: var(--white);
    margin-top: 2px;
  }
  .gold-tab {
    position: absolute;
    right: 0; top: 22px;
    width: 30px; height: 52px;
    background: var(--gold);
  }
  .mark-plate {
    position: absolute;
    right: 70px; top: 118px;
    width: 118px; height: 118px;
    background: var(--white);
    opacity: 0.08;
  }
  .card-front .brand {
    position: absolute;
    left: 42px; top: 118px;
    font-size: 21px;
  }
  .card-front .brand-square { width: 14px; height: 14px; }

  .contact {
    position: absolute;
    left: 42px; top: 172px;
    list-style: none;
    color: var(--white);
    font-size: 15px;
    line-height: 1.55;
  }
  .contact li { display: flex; align-items: center; gap: 10px; }
  .contact svg { width: 14px; height: 14px; flex: none; }
</style>
</head>
<body>

  <section class="card card-back" aria-label="Card back">
    <div class="brand"><span class="brand-square"></span>Harbor Crestline</div>
  </section>

  <section class="card card-front" aria-label="Card front">
    <svg class="swoosh" viewBox="0 0 600 343" preserveAspectRatio="none" aria-hidden="true">
      <defs>
        <linearGradient id="orangeFill" x1="0" y1="1" x2="1" y2="0">
          <stop offset="0" stop-color="#ea5a2a"/>
          <stop offset="1" stop-color="#f07a28"/>
        </linearGradient>
      </defs>
      <path d="M600 120 C500 150 470 230 420 270 C380 300 300 330 190 343 L600 343 Z" fill="url(#orangeFill)"/>
      <path d="M470 200 C420 270 330 300 110 320 L120 343 C300 315 420 285 470 200 Z" fill="var(--orange-light)"/>
      <path d="M470 200 C430 280 340 315 125 335 L130 343 C330 325 440 290 470 200 Z" fill="var(--navy)"/>
    </svg>

    <div class="gold-tab"></div>
    <div class="name-block">
      <p class="name">Dorian Fenwick</p>
      <p class="role">Founder + CEO</p>
    </div>
    <div class="mark-plate" aria-hidden="true"></div>

    <div class="brand"><span class="brand-square"></span>Harbor Crestline</div>

    <ul class="contact">
      <li>
        <svg viewBox="0 0 24 24" aria-hidden="true"><path fill="#d3a64a" d="M6.6 10.8a15 15 0 0 0 6.6 6.6l2.2-2.2a1 1 0 0 1 1-.25 11.4 11.4 0 0 0 3.6.6 1 1 0 0 1 1 1V20a1 1 0 0 1-1 1A17 17 0 0 1 3 4a1 1 0 0 1 1-1h3.5a1 1 0 0 1 1 1c0 1.25.2 2.45.6 3.6a1 1 0 0 1-.25 1z"/></svg>
        (833) 427-2731
      </li>
      <li>
        <svg viewBox="0 0 24 24" aria-hidden="true"><path fill="#d3a64a" d="M2 5h20v14H2z M2 5l10 8 10-8" stroke="#0f1a40" stroke-width="1.5"/></svg>
        dorian@theharborcrestline.com
      </li>
      <li>
        <svg viewBox="0 0 24 24" aria-hidden="true"><circle cx="12" cy="12" r="10" fill="#d3a64a"/><path d="M2 12h20M12 2c3 3 3 17 0 20M12 2c-3 3-3 17 0 20" stroke="#0f1a40" stroke-width="1.5" fill="none"/></svg>
        www.theharborcrestline.com
      </li>
    </ul>
  </section>

</body>
</html>
```